New website design and logo for FlintBoro.com to help ignite the website sales.

Hi designers,

Flintboro is a new welding brand that is selling welding equipement.

Currently I have around 5 to 10 products. The issue is that the site itself does not do that much of sales. So I have to do something about the seo etc. but that is out of scope for the design.

What is in scope is to comeup with a new logo and website look and feel that is in line with the customers.

men, non professionals, garage, home improvements, perhaps sme ( small mediul entreprice business that want to start in the welding industry.

Products are midrange prices and quality. The look and feel must breath cool stuff, sexy ( women in working cloths carrying welding gloves, other protection gear and weldels)

The wedsite is build in wordpress with the Kora theme. I am an IT guy myself withhout any creativity in me :( so if you can help me with that that would be great.

Please have a quick look at flintboro.com

Best regards,
Joris

Target Market(s)

non professional welders that do metal work in there garage

Coding

Coded - Design and coding required

Number of Pages Required

3 page

Font styles to use
Sans Serif

Colors
0355a3
ffc214

Requirements
Must have
• I would like to see a new homepage and product page design together with a new logo.
Nice to have
• shop design

```html
<!DOCTYPE html>
<html lang="en">
<head>
<meta charset="utf-8">
<title>Flintboro — Welding Equipment</title>
<link rel="stylesheet" href="https://fonts.googleapis.com/css2?family=Montserrat:wght@700;800&family=Roboto:ital,wght@0,400;0,500;0,700;1,400&display=swap">
<style>
:root{
  --blue:#0355a3;
  --blue-bright:#1a6fd1;
  --yellow:#ffc214;
  --orange:#f7a600;
  --ink:#1b1b1b;
  --muted:#666;
  --card-bg:#f4f4f4;
}
*{box-sizing:border-box;margin:0;padding:0}
html,body{width:1200px;height:3824px;overflow:hidden}
body{position:relative;font-family:'Roboto',sans-serif;color:var(--ink);background:#fff}
.abs{position:absolute}
.heading{font-family:'Montserrat',sans-serif;font-weight:800;text-transform:uppercase}

/* header */
.brand{left:107px;top:52px;display:flex;align-items:center;gap:10px}
.brand i{width:18px;height:18px;background:var(--yellow)}
.brand span{font-family:'Montserrat',sans-serif;font-weight:800;font-size:22px;color:var(--blue);letter-spacing:.5px}
.topbar{left:285px;top:22px;font-size:13px;font-weight:700}
.topbar em{font-style:normal;color:var(--orange);font-weight:400}
.lang{top:22px;font-size:13px;font-weight:500;color:#444}
.flag{left:867px;top:21px;width:24px;height:15px;background:repeating-linear-gradient(#c8102e 0 2px,#fff 2px 4px)}
.flag::before{content:"";position:absolute;left:0;top:0;width:10px;height:8px;background:var(--blue)}
.nav{left:285px;top:85px;display:flex;gap:24px;font-size:13px;font-weight:700;text-transform:uppercase}
.nav .active{color:var(--orange)}
.tool{top:70px;text-align:center;font-size:12px;font-weight:700;color:#555;text-transform:uppercase}
.tool svg{display:block;margin:0 auto 8px}

/* hero */
.hero{left:0;top:135px;width:1200px;height:720px;background:linear-gradient(110deg,#3a3a3c 0%,#2c323c 40%,#3c4452 70%,#4a4f58 100%)}
.hero-title{left:113px;top:300px;font-size:56px;color:#fff;letter-spacing:1px}
.hero-text{left:113px;top:390px;width:480px;font-size:14px;line-height:26px;color:#fff}
.btn{display:inline-flex;align-items:center;gap:8px;font-size:13px;font-weight:700;text-transform:uppercase;border-radius:30px}
.hero-btn{left:117px;top:463px;height:52px;padding:0 26px;background:var(--yellow);color:#fff;box-shadow:0 0 0 3px #fff,0 0 0 5px var(--blue)}
.dots{left:1140px;top:372px;display:flex;flex-direction:column;gap:12px}
.dots i{width:9px;height:9px;border-radius:50%;background:#fff}
.dots i.on{background:transparent;border:2px solid #fff}
.wave{left:0;top:575px;width:1200px;height:285px}

/* sections */
.section-title{width:1200px;left:0;text-align:center;font-size:33px;color:var(--ink)}
.card{width:236px;height:308px;background:#fff;box-shadow:0 2px 8px rgba(0,0,0,.12)}
.card .pic{height:221px}
.card .info{display:flex;justify-content:space-between;padding:18px 14px 0 18px;font-size:13px;color:#555}
.card .info b{color:var(--blue);font-size:12px}
.card .ship{display:flex;align-items:center;gap:10px;padding:22px 14px 0 18px;font-size:9px;font-weight:500;text-transform:uppercase;color:#333}
.card .ship .cart{margin-left:auto;width:20px;height:20px;border-radius:50%;border:2px solid var(--orange)}
.arrow{width:40px;height:40px;border-radius:50%;border:1px solid #ccc;background:#fff;display:flex;align-items:center;justify-content:center}
.pic-red{background:linear-gradient(160deg,#f4f4f4 10%,#c9584a 55%,#f4f4f4 95%)}
.pic-steel{background:linear-gradient(160deg,#f4f4f4 10%,#9fb3cc 55%,#f4f4f4 95%)}
.pic-black{background:linear-gradient(160deg,#f4f4f4 10%,#5a5a5e 55%,#f4f4f4 95%)}
.pic-olive{background:linear-gradient(160deg,#f4f4f4 10%,#5c6552 55%,#f4f4f4 95%)}
.pic-brown{background:linear-gradient(160deg,#f4f4f4 10%,#5a4238 55%,#f4f4f4 95%)}
.pic-glove{background:linear-gradient(160deg,#f4f4f4 10%,#8a86a8 50%,#e2bf70 70%,#f4f4f4 95%)}

/* promo band */
.promo{left:0;top:1351px;width:1200px;height:374px;background:linear-gradient(100deg,#f2a300,#ffc214 60%,#f5ab00)}
.promo .gloves{left:180px;top:40px;width:290px;height:290px;background:linear-gradient(135deg,rgba(43,63,196,.55),rgba(230,182,74,.5));border-radius:8px}
.promo h2{left:585px;top:70px;font-size:35px;line-height:35px;color:#fff}
.promo p{left:585px;top:155px;width:470px;font-size:13px;line-height:25px;color:#fff;font-weight:500}
.promo .btn{left:588px;top:232px;height:55px;padding:0 30px;background:#fff;color:var(--orange);border:3px solid var(--blue)}

/* testimonial */
.clients{left:0;top:2328px;width:1200px;height:350px;background:linear-gradient(110deg,#0b5fc0,#1a6fd1 50%,#0a56ad)}
.clients h2{left:110px;top:85px;font-size:35px;line-height:45px;color:#fff}
.clients .lead{left:111px;top:185px;width:290px;font-size:15px;line-height:27px;color:#fff}
.portrait{left:452px;top:77px;width:173px;height:198px;background:linear-gradient(#dfe6ee,#9aa8b8);border:3px solid #fff}
.quote-mark{left:598px;top:117px;width:47px;height:47px;background:var(--yellow);color:#fff;font-family:'Montserrat',sans-serif;font-size:40px;font-weight:800;text-align:center;line-height:56px}
.clients blockquote{left:694px;top:104px;width:440px;font-style:italic;font-size:15px;line-height:28px;color:#fff}
.byline{left:694px;top:205px;font-size:13px;font-weight:700;color:#fff;text-transform:uppercase;display:flex;gap:18px}
.pager{top:243px;width:45px;height:22px;background:#fff;display:flex;align-items:center;justify-content:center}

/* newsletter */
.newsletter{left:0;top:3265px;width:1200px;height:188px;background:linear-gradient(100deg,#f4a700,#ffc214 60%,#f3a200)}
.newsletter h2{left:101px;top:50px;font-size:28px;color:#fff}
.newsletter p{left:101px;top:95px;width:420px;font-size:14px;line-height:22px;color:#fff}
.newsletter .field{left:547px;top:71px;width:398px;height:50px;background:#fff;font-size:14px;color:#888;padding:16px 24px}
.newsletter .submit{left:945px;top:71px;width:153px;height:50px;background:var(--orange);color:#fff;border:2px solid #fff;font-size:13px;font-weight:700;display:flex;align-items:center;justify-content:center}

/* footer */
.footer{left:0;top:3453px;width:1200px;height:371px;background:linear-gradient(110deg,#0b5fc0,#1a6fd1 55%,#0a56ad);color:#fff}
.footer h4{font-size:13px;font-weight:700;text-transform:uppercase;top:56px}
.footer .about{left:109px;top:96px;width:290px;font-size:14px;line-height:26px}
.footer .about b{display:block;margin-top:16px;font-size:13px}
.footer ul{list-style:none;top:96px;font-size:14px;line-height:34px}
.footer li::before{content:"»";margin-right:16px}
.contact-row{left:857px;display:flex;align-items:center;gap:20px;font-size:14px;line-height:25px}
.contact-row .ic{width:36px;height:36px;border-radius:50%;border:2px solid #fff;display:flex;align-items:center;justify-content:center}
.footer .rule{left:113px;top:295px;width:975px;height:1px;background:rgba(255,255,255,.5)}
.footer .copy{left:0;width:1200px;top:327px;text-align:center;font-size:14px}
</style>
</head>
<body>

<!-- header -->
<div class="abs brand"><i></i><span>FLINTBORO</span></div>
<div class="abs topbar">FREE SHIPPING FROM <em>€ 30.00</em></div>
<div class="abs flag"></div>
<div class="abs lang" style="left:918px">ENG ⌄</div>
<div class="abs lang" style="left:1018px">USD ⌄</div>
<nav class="abs nav"><span class="active">Home</span><span>About Us</span><span>Our Products</span><span>Categories</span><span>Contact Us</span></nav>
<div class="abs tool" style="left:799px"><svg width="14" height="14" viewBox="0 0 14 14"><circle cx="7" cy="7" r="6" fill="none" stroke="#555" stroke-width="1.5"/><circle cx="7" cy="5.5" r="2" fill="#555"/></svg>My Accounts</div>
<div class="abs tool" style="left:932px"><svg width="14" height="14" viewBox="0 0 14 14"><path d="M7 12 1.5 6.5A3 3 0 0 1 7 3a3 3 0 0 1 5.5 3.5Z" fill="none" stroke="#555" stroke-width="1.5"/></svg>Wish List</div>
<div class="abs tool" style="left:1038px"><svg width="14" height="14" viewBox="0 0 14 14"><path d="M1 2h2l2 7h7l1.5-5H4" fill="none" stroke="#555" stroke-width="1.6"/><circle cx="6" cy="12" r="1.2" fill="#555"/><circle cx="11" cy="12" r="1.2" fill="#555"/></svg>(0) Items</div>

<!-- hero -->
<section class="abs hero" role="img" aria-label="Photo of a welder at work in a workshop"></section>
<h1 class="abs heading hero-title">Flintboro</h1>
<p class="abs hero-text">Lorem ipsum dolor sit amet, consectetur adipiscing elit, sed do eiusmod tempor incididunt ut labore et dolore magna aliqua.</p>
<a class="abs btn hero-btn">Shop Our Products <svg width="13" height="13" viewBox="0 0 13 13"><circle cx="6.5" cy="6.5" r="6.5" fill="#fff"/><path d="M5 3.5 8 6.5 5 9.5" stroke="#ffc214" stroke-width="2" fill="none"/></svg></a>
<div class="abs dots"><i></i><i></i><i class="on"></i><i></i><i></i></div>
<svg class="abs wave" viewBox="0 0 1200 285" preserveAspectRatio="none">
  <path d="M0 272 L0 242 C80 202 150 172 210 152 C320 117 420 187 520 122 C560 97 590 62 603 42 C616 62 646 97 686 122 C786 187 890 117 1000 152 C1060 172 1130 170 1200 218 L1200 272 Z" fill="var(--blue-bright)"/>
  <path d="M0 285 L0 262 C80 222 150 192 210 172 C320 140 420 210 520 144 C560 119 590 84 603 64 C616 84 646 119 686 144 C786 210 890 140 1000 172 C1060 192 1130 190 1200 240 L1200 285 Z" fill="#fff"/>
</svg>

<!-- products -->
<h2 class="abs heading section-title" style="top:850px">Our Products</h2>
<div class="abs arrow" style="left:25px;top:1078px"><svg width="12" height="16"><path d="M9 2 3 8l6 6" stroke="#222" stroke-width="2" fill="none"/></svg></div>
<div class="abs arrow" style="left:1135px;top:1078px"><svg width="12" height="16"><path d="M3 2l6 6-6 6" stroke="#222" stroke-width="2" fill="none"/></svg></div>
<div class="abs card" style="left:102px;top:944px"><div class="pic pic-red" role="img" aria-label="Red MIG welding machine"></div><div class="info"><span>MIG-250P</span><b>€ 795.00</b></div><div class="ship"><span style="color:var(--orange)">■</span>Same Day Delivery<span class="cart"></span></div></div>
<div class="abs card" style="left:356px;top:944px"><div class="pic pic-steel" role="img" aria-label="Blue and grey inverter welder"></div><div class="info"><span>MIG-2500</span><b>€ 745.00</b></div><div class="ship"><span style="color:var(--orange)">■</span>Same Day Delivery<span class="cart"></span></div></div>
<div class="abs card" style="left:609px;top:944px"><div class="pic pic-black" role="img" aria-label="Black welding helmet"></div><div class="info"><span>Welding helmet 180 view</span><b>€ 109.00</b></div><div class="ship"><span style="color:var(--orange)">■</span>Same Day Delivery<span class="cart"></span></div></div>
<div class="abs card" style="left:862px;top:944px"><div class="pic pic-olive" role="img" aria-label="Pair of black welding gloves"></div><div class="info"><span>Welding gloves Black</span><b>€ 22.40</b></div><div class="ship"><span style="color:var(--orange)">■</span>Same Day Delivery<span class="cart"></span></div></div>

<!-- promo -->
<section class="abs promo">
  <div class="abs gloves" role="img" aria-label="Blue and yellow leather welding gloves"></div>
  <h2 class="abs heading">Protect your hands<br>while welding</h2>
  <p class="abs">If you work with old worn out, hardened welding gloves, or if you weld with construction gloves (!) or worse, with bare hands</p>
  <a class="abs btn">Shop Our Products <svg width="13" height="13" viewBox="0 0 13 13"><circle cx="6.5" cy="6.5" r="6.5" fill="#f7a600"/><path d="M5 3.5 8 6.5 5 9.5" stroke="#fff" stroke-width="2" fill="none"/></svg></a>
</section>

<!-- best sellers -->
<h2 class="abs heading section-title" style="top:1811px">Best Sellers</h2>
<div class="abs arrow" style="left:25px;top:2040px"><svg width="12" height="16"><path d="M9 2 3 8l6 6" stroke="#222" stroke-width="2" fill="none"/></svg></div>
<div class="abs arrow" style="left:1135px;top:2040px"><svg width="12" height="16"><path d="M3 2l6 6-6 6" stroke="#222" stroke-width="2" fill="none"/></svg></div>
<div class="abs card" style="left:102px;top:1905px"><div class="pic pic-black" role="img" aria-label="Large view welding helmet"></div><div class="info" style="padding-left:8px"><span>Welding helmet large view</span><b>€ 89.00</b></div><div class="ship"><span style="color:var(--orange)">■</span>Same Day Delivery<span class="cart"></span></div></div>
<div class="abs card" style="left:356px;top:1905px"><div class="pic pic-brown" role="img" aria-label="Large black measuring triangle"></div><div class="info"><span>Large measuring triangle</span><b>€ 25.00</b></div><div class="ship"><span style="color:var(--orange)">■</span>Same Day Delivery<span class="cart"></span></div></div>
<div class="abs card" style="left:609px;top:1905px"><div class="pic pic-glove" role="img" aria-label="Blue and yellow welding gloves"></div><div class="info"><span>Welding gloves Blue</span><b>€ 22.40</b></div><div class="ship"><span style="color:var(--orange)">■</span>Same Day Delivery<span class="cart"></span></div></div>
<div class="abs card" style="left:862px;top:1905px"><div class="pic pic-brown" role="img" aria-label="Small black measuring triangle"></div><div class="info"><span>Small measuring triangle</span><b>€ 17.25</b></div><div class="ship"><span style="color:var(--orange)">■</span>Same Day Delivery<span class="cart"></span></div></div>

<!-- testimonial -->
<section class="abs clients">
  <h2 class="abs heading">What our<br>clients say</h2>
  <p class="abs lead">Lorem ipsum dolor sit amet, consectetur adipiscing elit, sed do eiusmod tempor incididunt ut labore et dolor</p>
  <div class="abs portrait" role="img" aria-label="Portrait of a customer in a suit"></div>
  <div class="abs quote-mark">“</div>
  <blockquote class="abs">" Sed ut perspiciatis unde omnis iste natus error sit voluptatem accusantium doloremque laudantium, totam rem aperiam, eaque ipsa quae ab illo inventore veritatis et "</blockquote>
  <div class="abs byline"><span>Dale Carver</span><span>|</span><span>Verified Review</span><span>|</span><span>★★★★★</span></div>
  <div class="abs pager" style="left:695px"><svg width="24" height="10"><path d="M22 5H3M7 1 3 5l4 4" stroke="#1a6fd1" stroke-width="2" fill="none"/></svg></div>
  <div class="abs pager" style="left:747px"><svg width="24" height="10"><path d="M2 5h19M17 1l4 4-4 4" stroke="#1a6fd1" stroke-width="2" fill="none"/></svg></div>
</section>

<!-- trending -->
<h2 class="abs heading section-title" style="top:2763px">Trending Now</h2>
<div class="abs arrow" style="left:25px;top:2991px"><svg width="12" height="16"><path d="M9 2 3 8l6 6" stroke="#222" stroke-width="2" fill="none"/></svg></div>
<div class="abs arrow" style="left:1135px;top:2991px"><svg width="12" height="16"><path d="M3 2l6 6-6 6" stroke="#222" stroke-width="2" fill="none"/></svg></div>
<div class="abs card" style="left:102px;top:2856px"><div class="pic pic-red" role="img" aria-label="Red MIG welding machine"></div><div class="info"><span>MIG-250P</span><b>€ 795.00</b></div><div class="ship"><span style="color:var(--orange)">■</span>Same Day Delivery<span class="cart"></span></div></div>
<div class="abs card" style="left:356px;top:2856px"><div class="pic pic-steel" role="img" aria-label="Blue and grey inverter welder"></div><div class="info"><span>MIG-2500</span><b>€ 745.00</b></div><div class="ship"><span style="color:var(--orange)">■</span>Same Day Delivery<span class="cart"></span></div></div>
<div class="abs card" style="left:609px;top:2856px"><div class="pic pic-black" role="img" aria-label="Black welding helmet"></div><div class="info"><span>Welding helmet 180 view</span><b>€ 109.00</b></div><div class="ship"><span style="color:var(--orange)">■</span>Same Day Delivery<span class="cart"></span></div></div>
<div class="abs card" style="left:862px;top:2856px"><div class="pic pic-olive" role="img" aria-label="Pair of black welding gloves"></div><div class="info"><span>Welding gloves Black</span><b>€ 22.40</b></div><div class="ship"><span style="color:var(--orange)">■</span>Same Day Delivery<span class="cart"></span></div></div>

<!-- newsletter -->
<section class="abs newsletter">
  <h2 class="abs heading">Newsletter Signup</h2>
  <p class="abs">At vero eos et accusamus et iusto odio dignissimos ducimus qui blanditiis praesentium voluptatum deleniti atque</p>
  <div class="abs field">Email Address</div>
  <div class="abs submit">SUBSCRIBE NOW</div>
</section>

<!-- footer -->
<footer class="abs footer">
  <h4 class="abs" style="left:109px">About Us</h4>
  <p class="abs about">Sed ut perspiciatis unde omnis iste natus error sit voluptatem accusantiudoloremque laudantium, totam rem aperiam, eaque ipsa quae ab illo inventore<b>READ MORE &nbsp;»</b></p>
  <h4 class="abs" style="left:472px">Quick Links</h4>
  <ul class="abs" style="left:472px"><li>Home</li><li>About Us</li><li>Our Products</li><li>Reviews</li><li>latest Blog</li></ul>
  <h4 class="abs" style="left:659px">Other Links</h4>
  <ul class="abs" style="left:659px"><li>Terms Of Use</li><li>Privacy Policy</li><li>Help Service</li><li>Contact Us</li><li>FAQ</li></ul>
  <h4 class="abs" style="left:857px">Contact Us</h4>
  <div class="abs contact-row" style="top:96px"><span class="ic"><svg width="14" height="16"><path d="M7 15s5-5 5-9A5 5 0 0 0 2 6c0 4 5 9 5 9Z" fill="none" stroke="#fff" stroke-width="1.6"/><circle cx="7" cy="6" r="1.8" fill="#fff"/></svg></span><span>48, Anvil Lane,<br>Millbrook</span></div>
  <div class="abs contact-row" style="top:161px"><span class="ic"><svg width="16" height="12"><rect x="1" y="1" width="14" height="10" fill="none" stroke="#fff" stroke-width="1.5"/><path d="M1 1l7 6 7-6" fill="none" stroke="#fff" stroke-width="1.5"/></svg></span><span>info@flintboro.com</span></div>
  <div class="abs contact-row" style="top:212px"><span class="ic"><svg width="14" height="14"><path d="M3 1l3 3-2 2a8 8 0 0 0 4 4l2-2 3 3-2 2C6 13 1 8 1 3Z" fill="#fff"/></svg></span><span>1 555 014 220</span></div>
  <div class="abs rule"></div>
  <div class="abs copy">© 2021 FlintBoro. All Rights Reserved</div>
</footer>

</body>
</html>
```